New Business Card Design Project

We require a business card design for Vexalund, a newly established Indian company.
Our focus is on the development, manufacturing, and export of a diverse array of pharmaceutical products on a global scale. The card should convey a professional appearance, as our primary markets are in Africa, China, and Southeast Asian nations.
We envision a two-sided business card, with the reverse side dedicated to a logo set against a solid color or an elegantly designed pattern. The corners should be rounded. We would appreciate seeing both horizontal and vertical design options. We trust the designer to utilize their expertise in creating this design.

The content for the business card is included in the attached Word file.

Target Market(s)

Our primary markets are in Africa, China, and Southeast Asian, Latin America, Maldives, Sri Lanka

Industry/Entity Type

Pharmaceutical Manufacturing and Export

Contact Information for Business Card

Colors

Designer to choose colors to be used in the design.

Requirements
Must have
• The reverse side of the business card features solely the logo along with the tagline, "Healing for Life."
Should not have
• The logo should not exceed two instances, encompassing both the front and back sides of the card.

```html
<!DOCTYPE html>
<html lang="en">
<head>
<meta charset="utf-8">
<title>Vexalund — Business Card</title>
<link rel="stylesheet" href="https://fonts.googleapis.com/css2?family=Open+Sans:wght@400;600;700&display=swap">
<style>
  :root {
    --backdrop: #262628;
    --card: #1f1f22;
    --blue: #2a9fd8;
    --coral: #e85d4a;
    --text: #d9d9dc;
  }
  * { box-sizing: border-box; margin: 0; padding: 0; }
  html, body {
    width: 1200px; height: 780px; overflow: hidden;
    background: var(--backdrop);
    font-family: "Open Sans", Arial, sans-serif;
  }
  .sheet {
    width: 1200px; height: 780px;
    display: flex; align-items: center; justify-content: center; gap: 40px;
  }
  .card {
    position: relative;
    width: 540px; height: 309px;
    background: var(--card);
    border-radius: 22px;
    overflow: hidden;
    box-shadow: 0 18px 40px rgba(0,0,0,.45);
    color: var(--text);
  }
  .wordmark {
    display: flex; align-items: center; gap: 12px;
    font-weight: 700; color: var(--blue); letter-spacing: .5px;
    white-space: nowrap;
  }
  .wordmark__dot {
    width: 18px; height: 18px; border-radius: 50%; background: var(--coral);
  }

  /* Front */
  .holder { position: absolute; left: 0; top: 30px; display: flex; }
  .holder__bar { width: 10px; height: 44px; background: var(--blue); margin-right: 12px; }
  .holder__name { font-size: 22px; line-height: 26px; white-space: nowrap; }
  .holder__first { color: var(--blue); font-weight: 700; }
  .holder__rest { color: var(--coral); font-weight: 400; }
  .holder__role { font-size: 11px; color: var(--text); letter-spacing: .5px; }
  .card--front .wordmark { position: absolute; right: 40px; top: 110px; font-size: 44px; }
  .address {
    position: absolute; left: 32px; bottom: 34px;
    font-size: 12px; line-height: 18px; color: var(--text); font-style: normal;
  }
  .contacts {
    position: absolute; right: 32px; bottom: 26px;
    list-style: none; font-size: 13px; line-height: 22px; text-align: right;
  }
  .contacts li { display: flex; align-items: center; justify-content: flex-end; gap: 10px; white-space: nowrap; }
  .contacts svg { width: 14px; height: 14px; flex: none; }

  /* Back */
  .card--back { display: flex; flex-direction: column; align-items: center; justify-content: center; }
  .card--back .wordmark { font-size: 50px; }
  .tagline { margin-top: 10px; font-size: 13px; color: var(--text); letter-spacing: .4px; }
</style>
</head>
<body>
<main class="sheet">
  <section class="card card--front" aria-label="Business card front">
    <div class="holder">
      <span class="holder__bar"></span>
      <div>
        <p class="holder__name"><span class="holder__first">Rohan</span> <span class="holder__rest">K. Valsekar</span></p>
        <p class="holder__role">CEO</p>
      </div>
    </div>

    <div class="wordmark"><span class="wordmark__dot"></span>Vexalund</div>

    <address class="address">
      14, Sunmarg Colony,<br>Nandpur, 440117, India
    </address>

    <ul class="contacts">
      <li>+918 315570914
        <svg viewBox="0 0 14 14"><rect x="3" y="1" width="8" height="12" rx="1.5" fill="none" stroke="var(--coral)" stroke-width="1.6"/></svg>
      </li>
      <li>www.vexalund.com
        <svg viewBox="0 0 14 14"><circle cx="7" cy="7" r="6" fill="var(--blue)"/><path d="M1 7h12M7 1c-3 3-3 9 0 12M7 1c3 3 3 9 0 12" stroke="var(--card)" stroke-width="1" fill="none"/></svg>
      </li>
      <li>rvalsekar@vexalund.com
        <svg viewBox="0 0 14 14"><rect x="1" y="3" width="12" height="9" rx="1" fill="var(--coral)"/><path d="M1.5 3.5 7 8l5.5-4.5" stroke="var(--card)" stroke-width="1.2" fill="none"/></svg>
      </li>
    </ul>
  </section>

  <section class="card card--back" aria-label="Business card back">
    <div class="wordmark"><span class="wordmark__dot"></span>Vexalund</div>
    <p class="tagline">Healing for Life.</p>
  </section>
</main>
</body>
</html>
```